Corporate Business Card

Very professional, Modern, Not to busy, include phone address email, website
(253) 617-4930, 18761 52nd Avenue S, Kent, WA 98047, martin@plumlinegroup.com, varkoworks.com

Target Market(s)

Manufacturing

Industry/Entity Type

Aero, machining, manufacturing, Off road racing

Contact Information for Business Card

Phone, address email, website

```html
<!DOCTYPE html>
<html lang="en">
<head>
<meta charset="utf-8">
<title>Varko Works – Business Card</title>
<link rel="stylesheet" href="https://fonts.googleapis.com/css2?family=Roboto:wght@400;700&family=Saira:wght@700&display=swap">
<style>
  :root {
    --backdrop: #2c2c2c;
    --card-black: #1f2022;
    --card-black-edge: #2e2f31;
    --navy: #2b3a6b;
    --red: #b82025;
    --silver: #a7a9ad;
    --logo-grey: #6a6c70;
    --white: #ffffff;
  }
  * { margin: 0; padding: 0; box-sizing: border-box; }
  html, body { width: 1200px; height: 1138px; overflow: hidden; }
  body {
    background: var(--backdrop);
    font-family: "Roboto", Arial, sans-serif;
    position: relative;
  }
  .card {
    position: absolute;
    width: 620px;
    height: 375px;
    border-radius: 14px;
    overflow: hidden;
  }
  .card-front {
    left: 274px; top: 186px;
    background: linear-gradient(160deg, var(--card-black) 40%, var(--card-black-edge));
  }
  .front-brand {
    position: absolute;
    left: 0; right: 0; top: 118px;
    text-align: center;
    font-weight: 700;
    font-size: 60px;
    letter-spacing: 2px;
    color: var(--logo-grey);
  }
  .front-web {
    position: absolute;
    left: 0; right: 0; top: 324px;
    text-align: center;
    font-size: 16px;
    letter-spacing: 10px;
    color: var(--white);
  }
  .front-web .accent { color: var(--red); }

  .card-back { left: 276px; top: 608px; background: var(--red); }
  .back-waves { position: absolute; inset: 0; }
  .back-brand {
    position: absolute;
    left: 0; right: 0; top: 52px;
    text-align: center;
    font-weight: 700;
    font-size: 44px;
    letter-spacing: 1px;
    color: var(--white);
  }
  .contact-list {
    position: absolute;
    right: 34px; top: 231px;
    list-style: none;
    text-align: right;
    color: var(--white);
    font-size: 17px;
    line-height: 24px;
  }
  .contact-list li { display: flex; justify-content: flex-end; align-items: center; gap: 14px; }
  .contact-list svg { width: 15px; height: 15px; fill: var(--white); }
  .contact-list .address { margin-top: 4px; margin-right: 0; }
  .holder-name {
    position: absolute;
    left: 35px; top: 282px;
    font-family: "Saira", Arial, sans-serif;
    font-weight: 700;
    font-size: 25px;
    line-height: 25px;
    color: var(--white);
    text-transform: uppercase;
  }
</style>
</head>
<body>
  <section class="card card-front">
    <div class="front-brand">VARKO WORKS</div>
    <div class="front-web">www.varko<span class="accent">works</span>.com</div>
  </section>

  <section class="card card-back">
    <svg class="back-waves" viewBox="0 0 620 375" preserveAspectRatio="none" aria-hidden="true">
      <path d="M0 0 H620 V150 C480 120 380 150 300 170 C200 192 80 185 0 158 Z" fill="var(--navy)"/>
      <path d="M0 136 C90 190 230 190 330 166 C430 142 520 128 620 150 V158 C520 138 430 152 330 176 C230 200 90 198 0 150 Z" fill="var(--silver)"/>
      <path d="M40 145 C150 185 250 180 300 170 C200 185 120 178 40 145 Z" fill="var(--silver)"/>
    </svg>
    <div class="back-brand">VARKO WORKS</div>
    <ul class="contact-list">
      <li>(253) 617-4930
        <svg viewBox="0 0 16 16"><path d="M3 2l3 0 1 3-2 1.5c1 2 2.5 3.5 4.5 4.5L11 9l3 1v3c0 .6-.4 1-1 1C7 14 2 9 2 3c0-.6.4-1 1-1z"/></svg>
      </li>
      <li>www.varkoworks.com
        <svg viewBox="0 0 16 16"><path d="M1 3h14v10H1z M2 4l6 5 6-5" fill="none" stroke="#fff" stroke-width="1.5"/></svg>
      </li>
      <li>martin@plumlinegroup.com
        <svg viewBox="0 0 16 16"><g fill="none" stroke="#fff" stroke-width="1.3"><circle cx="8" cy="8" r="6.5"/><ellipse cx="8" cy="8" rx="3" ry="6.5"/><path d="M1.5 8h13M3 4.5h10M3 11.5h10"/></g></svg>
      </li>
      <li class="address">18761 52nd Avenue S, Kent, WA 98047</li>
    </ul>
    <div class="holder-name">Martin<br>Hale</div>
  </section>
</body>
</html>
```